Website design for legal tech start up in Switzerland (B2B)

We are for a legal tech start up in Switzerland called KOVA. We have been running since August 2016. This will be our first live website.

We need a website designed and business card design for our start-up in Switzerland. We also need the Web design to be converted into HTML and CSS files.

Function of website:
• To inform potential customers of our services
• Form a key part of our digital marketing and sales footprint.
• Branding

Please find attached logo.
Updates

Project Deadline Extended Reason: Giving us time to review submissions and provide opportunity for more submissions. Added Thursday, February 16, 2017

Project Deadline Extended
Reason: Looking for more idea's not necessarily set on blue and grey colours only.

Target Market(s)

B2B tech powered legal services.

Industry/Entity Type

Legal

Contact Information for Business Card

Lean and slick design.

Coding

Coded - Design and coding required

Number of Pages Required

5+ page

Requirements
Must have
• VERY LEAN AND CLEAN DESIGN!
• We have received many great standard designs, but we are looking for something more out-of-the box: You can get inspiration from these designs: http://www.pixelvane.com/websites/clean/
• Thanks!!
• Easy content management system
• Well structured coding for additional development
• Responsive webpage for all types of devices
• SEO optimized
• Tabs (Home, services, team, careers, blog, contact us)
• Colour scheme complementary to logo
Nice to have
• Look and Design - Approachable, High-tech, Modern
• Easy to add chat bot capability in future
Should not have
• Too busy/ too much clutter
• Not take to long to load

```html
<!DOCTYPE html>
<html lang="en">
<head>
<meta charset="utf-8">
<title>KOVA – Legal Tech for Business</title>
<link href="https://fonts.googleapis.com/css2?family=Roboto:ital,wght@0,400;0,500;0,700;1,400&display=swap" rel="stylesheet">
<style>
:root{
  --blue:#3a5ca6;
  --blue-light:#5b80c6;
  --navy:#2b4787;
  --ink:#222;
  --muted:#666;
  --page:#fff;
  --soft:#f4f5f8;
  --line:#2f5597;
  --rule:#ddd;
}
*{box-sizing:border-box;margin:0;padding:0}
html,body{width:1200px;height:2233px;overflow:hidden}
body{font-family:'Roboto',sans-serif;color:var(--ink);background:var(--page);position:relative}
.row{position:absolute;left:52px;width:1096px}
.dotted{border-top:2px dotted var(--line);position:absolute;left:52px;width:1096px}

/* hero */
.hero{position:absolute;top:0;left:0;width:1200px;height:543px;background:linear-gradient(120deg,#4a4e55 0%,#2a2e35 45%,#3d4047 70%,#55585d 100%)}
.hero-photo{position:absolute;inset:0}
.topbar{position:absolute;top:0;left:0;width:1200px;height:66px;background:rgba(30,32,36,.45)}
.brand{position:absolute;left:54px;top:12px;font-size:38px;font-weight:500;letter-spacing:4px;color:#fff}
.nav{position:absolute;left:345px;top:23px;display:flex;gap:36px}
.nav a{color:#fff;text-decoration:none;font-size:15px;font-weight:500}
.btn-chat,.btn-eval{position:absolute;top:15px;height:34px;border-radius:17px;font-size:14px;font-weight:500;display:flex;align-items:center;justify-content:center}
.btn-chat{left:970px;width:65px;border:2px solid #fff;color:#fff}
.btn-eval{left:1040px;width:113px;background:#fff;color:#222}
.hero-copy{position:absolute;top:230px;left:0;width:1200px;text-align:center;color:#fff}
.hero-copy h1{font-size:20px;font-weight:700;margin-bottom:14px}
.hero-copy p{font-size:11px;line-height:22px;width:430px;margin:0 auto 16px;opacity:.9}
.btn-more{display:inline-block;border:2px solid #fff;border-radius:3px;padding:9px 14px;font-size:12px;font-weight:500}

/* welcome */
.welcome{position:absolute;top:543px;left:0;width:1200px;height:161px;background:linear-gradient(90deg,var(--blue),var(--blue-light));color:#fff}
.welcome-left{position:absolute;left:52px;top:22px;width:530px;text-align:center}
.welcome-left h2{font-size:21px;font-weight:500;padding-bottom:12px;border-bottom:1px dashed rgba(255,255,255,.8)}
.welcome-left p{font-size:13px;font-weight:700;line-height:19px;margin-top:14px}
.welcome-divider{position:absolute;left:599px;top:19px;width:2px;height:124px;background:rgba(255,255,255,.8)}
.welcome-right{position:absolute;left:620px;top:20px;width:540px;text-align:center;font-size:12.5px;line-height:19.5px}

/* tabs & services */
.tabs{position:absolute;top:716px;left:0;width:1200px;display:flex;justify-content:center}
.tab{font-size:15px;font-weight:500;padding:13px 18px;margin:0 8px;border:1px solid transparent;border-radius:3px}
.tab.active{border-color:var(--line);color:var(--line)}
.services{top:797px;display:flex;gap:28px}
.service{position:relative;width:253px;height:168px}
.service-photo{position:absolute;top:22px;left:0;width:253px;height:124px;border-radius:4px}
.service-icon{position:absolute;top:0;left:103px;width:46px;height:46px;border-radius:50%;background:var(--navy);border:3px solid #fff;display:flex;align-items:center;justify-content:center}
.service-label{position:absolute;top:127px;left:10px;width:233px;height:40px;border-radius:3px;background:linear-gradient(90deg,var(--navy),var(--blue-light));color:#fff;font-size:16px;font-weight:500;display:flex;align-items:center;justify-content:center}

/* mail band */
.mailband{position:absolute;top:987px;left:0;width:1200px;height:87px;background:linear-gradient(90deg,var(--navy),var(--blue-light));color:#fff}
.mailband svg{position:absolute;left:52px;top:28px}
.mail-label{position:absolute;left:113px;top:36px;font-size:13px;font-weight:500}
.field{position:absolute;top:27px;height:32px;width:253px;background:#fff;border-radius:3px;color:#999;font-size:12px;padding:9px 14px}
.submit{position:absolute;top:27px;left:1056px;width:94px;height:32px;background:#fff;border-radius:3px;color:#111;font-size:13px;font-weight:700;display:flex;align-items:center;justify-content:center}

/* sections */
.section-title{position:absolute;left:0;width:1200px;text-align:center;font-size:21px;font-weight:700;color:#222}
.section-title span{color:var(--line)}
.posts{top:1157px;display:flex;gap:28px}
.post{width:253px;height:356px;background:var(--soft)}
.post-photo{height:190px}
.post-body{padding:14px 19px 0}
.post-body h3{font-size:19px;font-weight:500;margin-bottom:9px;white-space:nowrap}
.post-body p{font-size:13px;line-height:19.5px;color:var(--muted);height:76px;border-bottom:1px dotted #bbb}
.post-meta{display:flex;justify-content:space-between;font-size:11px;color:#555;margin-top:14px}

.testimonials{position:absolute;top:1538px;left:0;width:1200px;height:212px;background:var(--soft)}
.quote{position:absolute;top:102px;font-size:12.5px;font-style:italic;line-height:19px;color:#555;width:405px}
.quote b{display:block;font-style:normal;font-weight:500;color:#222;margin-top:10px}
.avatar{position:absolute;top:102px;width:76px;height:76px;border-radius:50%;background:linear-gradient(135deg,#d9c7b8,#8b7f78)}
.quote-divider{position:absolute;left:599px;top:104px;height:72px;border-left:2px dotted var(--line)}

.likebar{position:absolute;top:1750px;left:0;width:1200px;height:70px}
.likebar .rule{position:absolute;top:35px;left:66px;width:1068px;border-top:1px solid var(--rule)}
.like-pill{position:absolute;left:378px;top:12px;width:446px;height:46px;border:1px solid var(--rule);border-radius:23px;background:#fff}
.like-pill .sep{position:absolute;left:55px;top:0;height:44px;border-left:1px solid var(--rule)}
.like-pill .thumb{position:absolute;left:17px;top:13px}
.like-btn{position:absolute;left:118px;top:14px;width:48px;height:18px;background:#4267b2;border-radius:2px;color:#fff;font-size:10px;font-weight:700;display:flex;align-items:center;justify-content:center}
.like-text{position:absolute;left:172px;top:16px;font-size:10px;color:#333}

/* footer */
.footer{position:absolute;top:1820px;left:0;width:1200px;height:413px;background:linear-gradient(120deg,var(--navy),var(--blue-light));color:#fff}
.footer h4{position:absolute;top:30px;font-size:17px;font-weight:700}
.contact{position:absolute;left:52px;top:70px;width:260px;font-size:13px;line-height:20px}
.contact p{margin-bottom:14px}
.socials{display:flex;gap:12px;margin-top:4px}
.socials i{width:13px;height:13px;border-radius:50%;background:#fff;display:block}
.map{position:absolute;left:333px;top:71px;width:535px;height:226px;background:linear-gradient(135deg,#e8e4d8,#c9d9ec 55%,#aac8e8)}
.about{position:absolute;left:895px;top:70px;width:254px;font-size:13px;line-height:20px}
.about p{margin-bottom:14px}
.footer-rule{position:absolute;left:52px;top:350px;width:1096px;border-top:1px solid rgba(255,255,255,.6)}
.footer-bottom{position:absolute;top:375px;font-size:12px;font-weight:700}
.footer-brand{position:absolute;left:0;width:1200px;top:363px;text-align:center;font-size:32px;font-weight:500;letter-spacing:4px}
</style>
</head>
<body>

<header class="hero">
  <div class="hero-photo" role="img" aria-label="Photo of business people in a meeting"></div>
  <div class="topbar">
    <div class="brand">KOVA</div>
    <nav class="nav"><a>HOME</a><a>SERVICES</a><a>TEAM</a><a>CAREERS</a><a>BLOG</a><a>CONTACT</a></nav>
    <div class="btn-chat">Chat</div>
    <div class="btn-eval">Free Evaluation</div>
  </div>
  <div class="hero-copy">
    <h1>Tech-Powered Legal Help for Business</h1>
    <p>Swiss legal experts and smart software working as one team. We help companies review contracts, stay compliant and handle routine legal work faster, with clear fixed prices.</p>
    <span class="btn-more">LEARN MORE</span>
  </div>
</header>

<section class="welcome">
  <div class="welcome-left">
    <h2>Welcome! To KOVA Legal Tech</h2>
    <p>Legal services built for companies, powered by technology.<br>We have a range of services to help in-house lawyers. Take a look and see how we can help you and your team.</p>
  </div>
  <div class="welcome-divider"></div>
  <div class="welcome-right">Founded in Switzerland in 2016, KOVA combines experienced lawyers with automation to take routine work off your desk. Our tools draft, review and track documents so your team can focus on the decisions that matter.<br>Every engagement starts with a free evaluation. We map your legal workload, show where software saves time and agree a fixed price before any work begins, so there are no surprises.</div>
</section>

<div class="tabs">
  <span class="tab active">Contract Review</span><span class="tab">Compliance</span><span class="tab">In House legal</span><span class="tab">Data Protection</span>
</div>
<div class="dotted" style="top:774px"></div>

<div class="row services">
  <div class="service">
    <div class="service-photo" role="img" aria-label="Photo of a contract being signed" style="background:linear-gradient(135deg,#6b5a50,#c9b8a8)"></div>
    <div class="service-icon"><svg width="18" height="20" viewBox="0 0 18 20"><path d="M3 1 H11 L15 5 V19 H3 Z" fill="none" stroke="#fff" stroke-width="2"/><path d="M6 10 H12 M6 14 H12" stroke="#fff" stroke-width="2"/></svg></div>
    <div class="service-label">Contract Review</div>
  </div>
  <div class="service">
    <div class="service-photo" role="img" aria-label="Photo of documents on an office desk" style="background:linear-gradient(135deg,#e8dccb,#b89a72)"></div>
    <div class="service-icon"><svg width="20" height="20" viewBox="0 0 20 20"><path d="M3 10 L8 15 L17 5" fill="none" stroke="#fff" stroke-width="2.5"/></svg></div>
    <div class="service-label">Compliance</div>
  </div>
  <div class="service">
    <div class="service-photo" role="img" aria-label="Photo of city office towers" style="background:linear-gradient(180deg,#9cc0e6,#5b6f86)"></div>
    <div class="service-icon"><svg width="20" height="20" viewBox="0 0 20 20"><rect x="3" y="11" width="3" height="6" fill="#fff"/><rect x="8.5" y="7" width="3" height="10" fill="#fff"/><rect x="14" y="3" width="3" height="14" fill="#fff"/></svg></div>
    <div class="service-label">Capital Market</div>
  </div>
  <div class="service">
    <div class="service-photo" role="img" aria-label="Photo of a laptop with secure data on screen" style="background:linear-gradient(135deg,#7a6a66,#3d5a80)"></div>
    <div class="service-icon"><svg width="18" height="20" viewBox="0 0 18 20"><path d="M9 1 L16 4 V10 C16 14 13 17 9 19 C5 17 2 14 2 10 V4 Z" fill="none" stroke="#fff" stroke-width="2"/></svg></div>
    <div class="service-label">Data Protection</div>
  </div>
</div>

<section class="mailband">
  <svg width="36" height="32" viewBox="0 0 36 32"><path d="M2 14 L34 2 L26 30 L16 20 Z M16 20 L34 2" fill="none" stroke="#fff" stroke-width="2" stroke-linejoin="round"/></svg>
  <span class="mail-label">Feel Free to Mail</span>
  <div class="field" style="left:240px">Full Name *</div>
  <div class="field" style="left:512px">Phone Number *</div>
  <div class="field" style="left:784px">Your Email *</div>
  <div class="submit">SUBMIT</div>
</section>

<h2 class="section-title" style="top:1084px">Latest <span>Blog &amp; Posts</span></h2>
<div class="dotted" style="top:1122px"></div>

<div class="row posts">
  <article class="post">
    <div class="post-photo" role="img" aria-label="Photo of a person walking into an office" style="background:linear-gradient(135deg,#5a3e2c,#a57448)"></div>
    <div class="post-body"><h3>Smarter NDAs</h3><p>How automated drafting cuts review time for standard agreements in half...</p><div class="post-meta"><span>▦ 22 June, 2017</span><span>● 0</span></div></div>
  </article>
  <article class="post">
    <div class="post-photo" role="img" aria-label="Photo of a coffee carafe on a desk" style="background:linear-gradient(135deg,#d8d6d0,#7e7a72)"></div>
    <div class="post-body"><h3>Video: Legal Ops</h3><p>A short walk through how in-house teams run legal work like a product...</p><div class="post-meta"><span>▦ 22 June, 2017</span><span>● 0</span></div></div>
  </article>
  <article class="post">
    <div class="post-photo" role="img" aria-label="Photo of a meeting table against a brick wall" style="background:linear-gradient(135deg,#8a5a44,#3f2e26)"></div>
    <div class="post-body"><h3>Swiss Data Law</h3><p>What the revised Swiss data protection act means for your company...</p><div class="post-meta"><span>▦ 22 June, 2017</span><span>● 0</span></div></div>
  </article>
  <article class="post">
    <div class="post-photo" role="img" aria-label="Photo of a leather wallet on a desk" style="background:linear-gradient(135deg,#d9d1c4,#6b4a32)"></div>
    <div class="post-body"><h3>Fixed Fees</h3><p>Why predictable pricing is changing how businesses buy legal services...</p><div class="post-meta"><span>▦ 22 June, 2017</span><span>● 3</span></div></div>
  </article>
</div>

<section class="testimonials">
  <h2 class="section-title" style="top:18px">What <span>People Say</span></h2>
  <div class="dotted" style="top:55px"></div>
  <div class="quote" style="left:56px;text-align:right">KOVA took our contract backlog from weeks to days. The platform is simple to use and the lawyers behind it answer quickly, so our small legal team finally keeps pace with sales.<b>Marc Berger, Operations Manager</b></div>
  <div class="avatar" role="img" aria-label="Portrait photo of client" style="left:490px"></div>
  <div class="quote-divider"></div>
  <div class="avatar" role="img" aria-label="Portrait photo of client" style="left:633px"></div>
  <div class="quote" style="left:740px">Clear fixed prices and a dashboard that shows where every matter stands. It feels like having an extra in-house counsel without the overhead of hiring one.<b>Anna Keller, General Counsel</b></div>
</section>

<div class="likebar">
  <div class="rule"></div>
  <div class="like-pill">
    <svg class="thumb" width="20" height="20" viewBox="0 0 20 20"><path d="M2 9 H5 V18 H2 Z M5 9 L9 2 C11 2 11 4 10.5 7 H17 L15.5 18 H5" fill="none" stroke="#bbb" stroke-width="1.5"/></svg>
    <div class="sep"></div>
    <div class="like-btn">✓ Like</div>
    <span class="like-text">You and 4k others like this.</span>
  </div>
</div>

<footer class="footer">
  <h4 style="left:52px">Contact Us</h4>
  <h4 style="left:543px">Headquarters</h4>
  <h4 style="left:895px">About Team</h4>
  <div class="contact">
    <p>Please feel free to contact us for any issue. Our staff is available to you from 9AM until 5PM on weekdays.</p>
    <p><b>Phone:</b> +41 22 555 01 90</p>
    <p><b>Office:</b> Company Address Here</p>
    <p><b>Email:</b> hello@kova-legal.ch</p>
    <div class="socials"><i></i><i></i><i></i><i></i><i></i></div>
  </div>
  <div class="map" role="img" aria-label="Map showing the headquarters location"></div>
  <div class="about">
    <p>Our team brings together Swiss lawyers, engineers and designers who believe legal work can be faster, clearer and fairly priced for every business.</p>
    <p>We build tools we use ourselves every day, and we keep improving them with feedback from the companies we serve across Switzerland.</p>
  </div>
  <div class="footer-rule"></div>
  <div class="footer-brand">KOVA</div>
  <div class="footer-bottom" style="left:52px">Copyright © KOVA</div>
  <div class="footer-bottom" style="right:52px">All rights reserved</div>
</footer>

</body>
</html>
```